Mira Bloom Fitness Coaching Project

I am a personal trainer based in London. My services include one-on-one PT sessions, bootcamps.
I would like the design to be minimalistic. With light colours: white, pink, purple.
I specialise in weight loss, flexibility, mobility.

Tessa Brogan
Personal Trainer
Email: tessa.brogan@quellmail.com
tel: 07700218493
Instagram: Mira Bloom

Target Market(s)

adults, mostly females (age 18-50).

Industry/Entity Type

Fitness

Contact Information for Business Card

Tessa Brogan
Personal Trainer
tel: 07700218493
Instagram: Mira Bloom

Font styles to use
Serif

Colors
eea4c8
fbd4d5
fdf9cf
cfeae6
cee9f5

Requirements
Nice to have
• minimalistic style
• easy to read and remember

```html
<!DOCTYPE html>
<html lang="en">
<head>
<meta charset="utf-8">
<title>Mira Bloom Fitness Coaching – Business Card</title>
<link rel="stylesheet" href="https://fonts.googleapis.com/css2?family=Open+Sans:wght@400;700&display=swap">
<style>
  :root {
    --plum: #6d1042;
    --paper: #ffffff;
    --backdrop: #ececec;
    --ink: #3a3a3a;
    --blush: #f2c6c3;
    --rose: #f5b3c0;
    --hot-pink: #ef6fb8;
    --mint: #9fe0dc;
    --hair: #6e4330;
    --hair-light: #a8785c;
  }
  * { box-sizing: border-box; margin: 0; padding: 0; }
  html, body { width: 1200px; height: 900px; overflow: hidden; }
  body {
    background: var(--backdrop);
    font-family: "Open Sans", sans-serif;
    color: var(--ink);
    display: flex;
    flex-direction: column;
    align-items: center;
    justify-content: center;
    gap: 40px;
  }
  .card {
    position: relative;
    width: 620px;
    height: 354px;
    background: var(--paper);
    overflow: hidden;
    box-shadow: 0 6px 18px rgba(0,0,0,.12);
  }

  /* business name */
  .brand-name {
    font-family: "Open Sans", sans-serif;
    font-weight: 700;
    font-size: 22px;
    color: var(--plum);
    white-space: nowrap;
  }

  /* front */
  .card-front .brand-name { position: absolute; left: 40px; top: 40px; }
  .contact { position: absolute; left: 40px; top: 112px; }
  .contact-name {
    font-weight: 700; font-size: 17px; color: var(--plum);
    text-transform: uppercase; letter-spacing: .3px;
  }
  .contact-role { font-size: 12px; margin-bottom: 8px; }
  .contact-row { display: flex; align-items: center; gap: 8px; font-size: 12.5px; margin-top: 4px; }
  .contact-row svg { width: 12px; height: 12px; flex: none; }
  .icon-phone { fill: var(--plum); }
  .icon-mail { fill: none; stroke: var(--plum); stroke-width: 2.5; }
  .specialties-band {
    position: absolute; left: 0; right: 0; bottom: 0; height: 128px;
    background: var(--plum);
  }
  .specialties {
    position: absolute; left: 40px; top: 50px;
    display: flex; gap: 18px; list-style: none;
    color: #fff; font-size: 14px;
  }
  .specialties li::before { content: "● "; font-size: 10px; vertical-align: 2px; }
  .portrait {
    position: absolute; right: 95px; bottom: 0;
    width: 210px; height: 210px;
    background: linear-gradient(160deg, var(--hair-light) 0%, var(--hair) 60%, #d9c3c3 100%);
  }

  /* back */
  .scene {
    position: absolute; inset: 0 0 110px 0;
    background: linear-gradient(100deg, var(--blush) 0%, var(--rose) 45%, var(--hot-pink) 70%, var(--mint) 100%);
    opacity: .85;
  }
  .card-back .brand-name {
    position: absolute; left: 0; right: 0; top: 108px; text-align: center;
  }
  .social-band {
    position: absolute; left: 0; right: 0; bottom: 0; height: 110px;
    background: var(--plum);
    display: flex; align-items: center; justify-content: center; gap: 10px;
    color: #fff; font-size: 15px;
  }
  .social-band .handle-dot { width: 14px; height: 14px; background: #fff; border-radius: 3px; }
</style>
</head>
<body>

  <section class="card card-front">
    <p class="brand-name">Mira Bloom Fitness Coaching</p>

    <div class="contact">
      <p class="contact-name">Tessa Brogan</p>
      <p class="contact-role">Personal Trainer</p>
      <p class="contact-row">
        <svg class="icon-phone" viewBox="0 0 24 24"><path d="M6.6 10.8a15.1 15.1 0 0 0 6.6 6.6l2.2-2.2a1 1 0 0 1 1-.25 11.4 11.4 0 0 0 3.6.57 1 1 0 0 1 1 1V20a1 1 0 0 1-1 1A17 17 0 0 1 3 4a1 1 0 0 1 1-1h3.5a1 1 0 0 1 1 1c0 1.25.2 2.45.57 3.6a1 1 0 0 1-.25 1z"/></svg>
        07700218493
      </p>
      <p class="contact-row">
        <svg class="icon-mail" viewBox="0 0 24 24"><rect x="2" y="5" width="20" height="14"/><path d="M3 6l9 7 9-7"/></svg>
        tessa.brogan@quellmail.com
      </p>
    </div>

    <div class="specialties-band">
      <ul class="specialties">
        <li>Weight Loss</li>
        <li>Flexibility</li>
        <li>Mobility</li>
      </ul>
    </div>

    <div class="portrait" role="img" aria-label="Portrait photo of the trainer with long curly hair"></div>
  </section>

  <section class="card card-back">
    <div class="scene" role="img" aria-label="Photo of two women exercising outdoors by pink and turquoise walls"></div>
    <p class="brand-name">Mira Bloom Fitness Coaching</p>
    <div class="social-band">
      <span class="handle-dot"></span>
      <span class="handle">Mira Bloom</span>
    </div>
  </section>

</body>
</html>
```